Logo & Visitenkarte für Weinbauer
Zielgruppe
Ich bin Weinbauer und betreibe auch einen Buschenschank. Zielgruppe ist die Gastronomie und der (Durchschnitts-) Endverbraucher.
Aufgabenstellung
Unsere Betriebsstätte ist im Rebhügelgau Weinviertel (Österreich).
Wir wollen die Werte Tradition, Regional, Vertrauen und Bodenständigkeit vermitteln.
Unsere Kunden schätzen die Herkunft.
Das Logo soll als Firmenlogo und auch für die Weinetiketten verwendet werden können.

```html
<!DOCTYPE html>
<html lang="de">
<head>
<meta charset="utf-8">
<title>Weinbau Hollerer – Weinetikett</title>
<link rel="stylesheet" href="https://fonts.googleapis.com/css2?family=Barlow+Condensed:wght@400;600&display=swap">
<style>
  :root {
    --backdrop: #d9d9d9;
    --label-red: #6b2a2c;
    --label-red-dark: #5a2225;
    --gold: #c9a067;
    --hairline: #ead8d2;
  }
  html, body {
    margin: 0;
    padding: 0;
    overflow: hidden;
    background: var(--backdrop);
  }
  .canvas {
    width: 1164px;
    height: 1200px;
    position: relative;
    overflow: hidden;
    background: var(--backdrop);
  }
  .label-art {
    position: absolute;
    inset: 0;
  }
  .brand-name {
    font-family: "Barlow Condensed", sans-serif;
    font-weight: 400;
    font-size: 44px;
    letter-spacing: 1px;
    fill: var(--gold);
  }
  .label-copy {
    font-family: "Barlow Condensed", sans-serif;
    font-weight: 600;
    font-size: 15px;
    fill: var(--gold);
  }
</style>
</head>
<body>
<div class="canvas">
  <svg class="label-art" width="1164" height="1200" viewBox="0 0 1164 1200" xmlns="http://www.w3.org/2000/svg">
    <defs>
      <linearGradient id="labelShade" x1="0" x2="1" y1="0" y2="0">
        <stop offset="0" stop-color="var(--label-red-dark)"/>
        <stop offset="0.45" stop-color="var(--label-red)"/>
        <stop offset="1" stop-color="var(--label-red-dark)"/>
      </linearGradient>
    </defs>

    <!-- decorative rings -->
    <g class="deco-rings" fill="none" stroke="var(--label-red)" stroke-width="8">
      <circle cx="642" cy="120" r="38"/>
      <circle cx="880" cy="300" r="95"/>
      <circle cx="310" cy="980" r="95"/>
    </g>

    <!-- horizontal band -->
    <rect class="label-band" x="312" y="430" width="540" height="400" fill="url(#labelShade)"/>

    <!-- oval label body -->
    <rect class="label-oval" x="372" y="150" width="420" height="900" rx="210" fill="url(#labelShade)"/>
    <rect class="label-oval-line" x="388" y="166" width="388" height="868" rx="194" fill="none" stroke="var(--hairline)" stroke-width="2"/>

    <!-- brand mark -->
    <circle class="brand-dot" cx="582" cy="470" r="46" fill="none" stroke="var(--gold)" stroke-width="5"/>
    <text class="brand-name" x="582" y="592" text-anchor="middle">WEINBAU HOLLERER</text>

    <!-- label copy -->
    <g class="label-copy" text-anchor="middle">
      <text x="582" y="810">Lorem ipsum dolor sit amet, consetetur sadipscing</text>
      <text x="582" y="830">elitr, sed diam nonumy eirmod tempor invidunt ut</text>
      <text x="582" y="850">labore et dolore magna aliquyam erat, sed diam vo-</text>
      <text x="582" y="870">luptua. At vero eos et accusam et justo duo dolores</text>
      <text x="582" y="890">et ea rebum. Stet clita kasd gubergren, no sea</text>
      <text x="582" y="910">takimata sanctus est Lorem ipsum dolor sit amet.</text>
      <text x="582" y="930">Lorem ipsum dolor sit amet, consetetur sadipscing</text>
      <text x="582" y="950">elitr, sed diam nonumy eirmod tempor invidunt ut</text>
      <text x="582" y="970">labore et dolore magna aliquyam erat,</text>
    </g>
  </svg>
</div>
</body>
</html>
```